Web App Design Project

Need to provide graphical design of 2 web pages according to attached wireframes.

Colors should be adjusted for the 65+ population meaning not too bright.

App logo should be created as well - logo should represent long and good life.

Target Market(s)

65 years old and above

```html
<!DOCTYPE html>
<html lang="en">
<head>
<meta charset="utf-8">
<title>Vitalo – Medications</title>
<link href="https://fonts.googleapis.com/css2?family=Open+Sans:wght@400;600;700;800&display=swap" rel="stylesheet">
<style>
  :root{
    --navy:#0b3a68;
    --navy-light:#1f5f9c;
    --ink:#1a1a1a;
    --panel:#e4e5e7;
    --panel-line:#c3c5c8;
    --divider:#9a9da1;
    --white:#ffffff;
    --accent-blue:#2f6fb4;
    --pill-red:#b3121b;
    --pill-white:#f2f2f2;
    --tile-black:#0d0d0d;
  }
  *{box-sizing:border-box;margin:0;padding:0}
  html,body{width:1200px;height:767px;overflow:hidden;background:var(--white)}
  body{font-family:"Open Sans",Arial,sans-serif;color:var(--ink);position:relative}

  .app-header{position:absolute;left:0;top:0;width:1200px;height:92px;
    background:linear-gradient(to bottom,var(--navy-light),var(--navy));}
  .brand{position:absolute;left:22px;top:24px;display:flex;align-items:center;gap:8px;
    color:var(--white);font-weight:700;font-size:26px}
  .brand-mark{width:16px;height:16px;background:var(--white)}
  .user-name{position:absolute;left:172px;top:18px;color:var(--white);font-weight:700;font-size:38px;letter-spacing:.3px}
  .search-field{position:absolute;left:673px;top:19px;width:241px;height:54px;background:var(--white);
    border:3px solid #7d8a98;font-weight:700;font-size:30px;padding:3px 8px;color:var(--ink)}
  .header-btn{position:absolute;top:19px;height:54px;background:var(--white);border:3px solid #7d8a98;
    display:flex;align-items:center;justify-content:center;font-weight:800;font-size:30px;color:var(--ink)}
  .btn-search{left:933px;width:54px}
  .btn-help{left:1027px;width:54px}
  .btn-exit{left:1098px;width:88px}

  .time-panel{position:absolute;left:13px;top:101px;width:277px;height:482px;background:var(--panel);
    border:3px solid var(--panel-line);border-radius:12px}
  .time-panel h2{text-align:center;color:var(--navy);font-size:30px;font-weight:700;margin-top:10px}
  .time-slot{position:absolute;left:14px;width:244px;height:100px;border-top:3px solid var(--divider);
    display:flex;align-items:center;gap:16px;padding-left:22px;font-size:25px;font-weight:600}
  .time-slot svg{flex:none}

  .add-medication{position:absolute;left:335px;top:104px;display:flex;align-items:center;gap:12px;
    font-weight:700;font-size:17px}
  .settings{position:absolute;left:1114px;top:102px}

  .med-list{position:absolute;left:300px;top:158px;width:887px;height:425px;background:var(--panel);
    border:3px solid var(--panel-line);border-radius:12px}
  .med-row{position:absolute;left:28px;width:840px;height:104px;display:flex;align-items:center}
  .med-row + .med-row{border-top:3px solid var(--divider)}
  .mark-taken{width:214px;height:82px;background:var(--white);border:3px solid #9da0a4;border-radius:12px;
    display:flex;align-items:center;justify-content:center;font-size:22px;font-weight:600}
  .med-name{position:absolute;left:239px;font-size:23px;font-weight:700}
  .med-dose{position:absolute;left:525px;font-size:23px;font-weight:700}
  .med-pill{position:absolute;left:612px}
  .med-info{position:absolute;left:788px}

  .nav-bar{position:absolute;left:0;top:598px;width:1200px;height:169px}
  .nav-tile{position:absolute;top:0;width:158px;height:169px;background:var(--tile-black);padding:9px}
  .nav-inner{width:100%;height:100%;background:var(--white);display:flex;flex-direction:column;align-items:center;
    justify-content:flex-end;padding-bottom:4px}
  .nav-art{width:96px;height:90px;border-radius:8px;margin-bottom:6px}
  .nav-label{font-size:16px;font-weight:700;text-align:center;line-height:1.15}
</style>
</head>
<body>

<header class="app-header">
  <div class="brand"><span class="brand-mark"></span>Vitalo</div>
  <div class="user-name">Walter Greene</div>
  <div class="search-field">Search</div>
  <div class="header-btn btn-search" aria-label="Search">
    <svg width="40" height="40" viewBox="0 0 40 40"><circle cx="24" cy="15" r="10" fill="none" stroke="#2f6fb4" stroke-width="4"/><line x1="17" y1="22" x2="5" y2="35" stroke="#2f6fb4" stroke-width="5" stroke-linecap="round"/></svg>
  </div>
  <div class="header-btn btn-help">?</div>
  <div class="header-btn btn-exit">Exit</div>
</header>

<aside class="time-panel">
  <h2>Medications</h2>
  <div class="time-slot" style="top:70px">
    <svg width="58" height="40" viewBox="0 0 58 40"><path d="M12 30a17 17 0 0 1 34 0z" fill="#2f6fb4"/><g stroke="#2f6fb4" stroke-width="2"><line x1="29" y1="4" x2="29" y2="10"/><line x1="14" y1="12" x2="18" y2="16"/><line x1="44" y1="12" x2="40" y2="16"/><line x1="4" y1="24" x2="10" y2="24"/><line x1="48" y1="24" x2="54" y2="24"/></g><line x1="4" y1="32" x2="54" y2="32" stroke="#2f6fb4" stroke-width="2"/></svg>
    Morning
  </div>
  <div class="time-slot" style="top:168px">
    <svg width="50" height="50" viewBox="0 0 50 50"><circle cx="25" cy="25" r="11" fill="#2f6fb4"/><g stroke="#2f6fb4" stroke-width="2"><line x1="25" y1="2" x2="25" y2="10"/><line x1="25" y1="40" x2="25" y2="48"/><line x1="2" y1="25" x2="10" y2="25"/><line x1="40" y1="25" x2="48" y2="25"/><line x1="9" y1="9" x2="14" y2="14"/><line x1="36" y1="36" x2="41" y2="41"/><line x1="41" y1="9" x2="36" y2="14"/><line x1="14" y1="36" x2="9" y2="41"/></g></svg>
    Noon
  </div>
  <div class="time-slot" style="top:271px;padding-left:4px">
    <svg width="90" height="50" viewBox="0 0 90 50"><circle cx="58" cy="22" r="11" fill="#2f6fb4"/><g stroke="#2f6fb4" stroke-width="2"><line x1="58" y1="2" x2="58" y2="8"/><line x1="76" y1="22" x2="84" y2="22"/><line x1="72" y1="8" x2="68" y2="12"/><line x1="44" y1="8" x2="48" y2="12"/></g><path d="M6 40q0-10 12-9q4-10 16-6q10-4 14 6q12 0 12 9z" fill="#8fb3d9"/></svg>
    Afternoon
  </div>
  <div class="time-slot" style="top:373px;padding-left:40px">
    <svg width="40" height="50" viewBox="0 0 40 50"><path d="M28 4a21 21 0 1 0 0 42a17 17 0 0 1 0-42z" fill="#2f6fb4"/></svg>
    Night
  </div>
</aside>

<div class="add-medication">
  <svg width="44" height="44" viewBox="0 0 44 44"><circle cx="22" cy="22" r="20" fill="#eef1f5" stroke="#8d97a3" stroke-width="2"/><path d="M22 10v24M10 22h24" stroke="#2f6fb4" stroke-width="5"/></svg>
  Add Medication
</div>
<div class="settings" aria-label="Settings">
  <svg width="48" height="48" viewBox="0 0 48 48"><g fill="#2f6fb4" transform="translate(24 24)"><circle r="15"/><rect x="-4" y="-22" width="8" height="10"/><rect x="-4" y="-22" width="8" height="10" transform="rotate(45)"/><rect x="-4" y="-22" width="8" height="10" transform="rotate(90)"/><rect x="-4" y="-22" width="8" height="10" transform="rotate(135)"/><rect x="-4" y="-22" width="8" height="10" transform="rotate(180)"/><rect x="-4" y="-22" width="8" height="10" transform="rotate(225)"/><rect x="-4" y="-22" width="8" height="10" transform="rotate(270)"/><rect x="-4" y="-22" width="8" height="10" transform="rotate(315)"/></g><circle cx="24" cy="24" r="6" fill="#fff"/></svg>
</div>

<section class="med-list">
  <div class="med-row" style="top:8px">
    <div class="mark-taken">Mark as Taken</div>
    <span class="med-name">Medication_01 Name</span><span class="med-dose">4x</span>
    <svg class="med-pill" width="48" height="80" viewBox="0 0 48 80"><g transform="rotate(15 24 40)"><rect x="12" y="6" width="24" height="68" rx="12" fill="var(--pill-red)"/><path d="M12 40V18a12 12 0 0 1 24 0v22z" fill="var(--pill-white)" stroke="#bbb"/></g></svg>
    <svg class="med-info" width="40" height="40" viewBox="0 0 40 40"><circle cx="20" cy="20" r="19" fill="#2f6fb4"/><circle cx="20" cy="11" r="3" fill="#fff"/><rect x="17" y="17" width="6" height="15" fill="#fff"/></svg>
  </div>
  <div class="med-row" style="top:112px">
    <div class="mark-taken">Mark as Taken</div>
    <span class="med-name">Medication_02 Name</span><span class="med-dose">2x</span>
    <svg class="med-pill" width="56" height="56" viewBox="0 0 56 56"><circle cx="28" cy="28" r="25" fill="var(--pill-white)" stroke="#bbb"/><path d="M28 3a25 25 0 0 1 0 50z" fill="var(--pill-red)"/></svg>
    <svg class="med-info" width="40" height="40" viewBox="0 0 40 40"><circle cx="20" cy="20" r="19" fill="#2f6fb4"/><circle cx="20" cy="11" r="3" fill="#fff"/><rect x="17" y="17" width="6" height="15" fill="#fff"/></svg>
  </div>
  <div class="med-row" style="top:216px">
    <div class="mark-taken">Mark as Taken</div>
    <span class="med-name">Medication_03 Name</span><span class="med-dose">4x</span>
    <svg class="med-pill" width="80" height="48" viewBox="0 0 80 48"><g transform="rotate(-15 40 24)"><rect x="6" y="12" width="68" height="24" rx="12" fill="var(--pill-white)" stroke="#bbb"/><path d="M40 12H18a12 12 0 0 0 0 24h22z" fill="var(--pill-red)"/></g></svg>
    <svg class="med-info" width="40" height="40" viewBox="0 0 40 40"><circle cx="20" cy="20" r="19" fill="#2f6fb4"/><circle cx="20" cy="11" r="3" fill="#fff"/><rect x="17" y="17" width="6" height="15" fill="#fff"/></svg>
  </div>
  <div class="med-row" style="top:320px">
    <div class="mark-taken">Mark as Taken</div>
    <span class="med-name">Medication_04 Name</span><span class="med-dose">4x</span>
    <svg class="med-pill" width="56" height="56" viewBox="0 0 56 56"><circle cx="28" cy="28" r="25" fill="var(--pill-white)" stroke="#bbb"/><path d="M28 3a25 25 0 0 1 0 50z" fill="var(--pill-red)"/></svg>
    <svg class="med-info" width="40" height="40" viewBox="0 0 40 40"><circle cx="20" cy="20" r="19" fill="#2f6fb4"/><circle cx="20" cy="11" r="3" fill="#fff"/><rect x="17" y="17" width="6" height="15" fill="#fff"/></svg>
  </div>
</section>

<nav class="nav-bar">
  <div class="nav-tile" style="left:9px"><div class="nav-inner">
    <div class="nav-art" role="img" aria-label="Red and white pills icon" style="background:linear-gradient(135deg,#b3121b,#e9e9e9)"></div>
    <span class="nav-label">Medications</span></div></div>
  <div class="nav-tile" style="left:178px"><div class="nav-inner">
    <div class="nav-art" role="img" aria-label="Thermometer icon" style="background:linear-gradient(135deg,#7fa3cc,#b3121b)"></div>
    <span class="nav-label">Home<br>Measurements</span></div></div>
  <div class="nav-tile" style="left:350px"><div class="nav-inner">
    <div class="nav-art" role="img" aria-label="Calendar icon" style="background:linear-gradient(180deg,#1f5f9c,#0b3a68)"></div>
    <span class="nav-label">My Schedule</span></div></div>
  <div class="nav-tile" style="left:521px"><div class="nav-inner">
    <div class="nav-art" role="img" aria-label="Stethoscope icon" style="background:linear-gradient(135deg,#b3121b,#2f6fb4)"></div>
    <span class="nav-label">Lab Tests<br>Results</span></div></div>
  <div class="nav-tile" style="left:693px"><div class="nav-inner">
    <div class="nav-art" role="img" aria-label="Checklist clipboard icon" style="background:linear-gradient(135deg,#0b3a68,#b3121b)"></div>
    <span class="nav-label">Checkups &amp;<br>Procedures</span></div></div>
  <div class="nav-tile" style="left:863px"><div class="nav-inner">
    <div class="nav-art" role="img" aria-label="Profile ID card icon" style="background:linear-gradient(180deg,#2f6fb4,#1f5f9c)"></div>
    <span class="nav-label">My Profile</span></div></div>
  <div class="nav-tile" style="left:1036px"><div class="nav-inner">
    <div class="nav-art" role="img" aria-label="Health care provider icon" style="background:linear-gradient(180deg,#7fa3cc,#1f5f9c)"></div>
    <span class="nav-label">My Health Care<br>Providers</span></div></div>
</nav>

</body>
</html>
```